Roofing Contractor business card redesign

I want to redesign my business card with a fresh, eye catching concept

Target Market(s)

Residential Roofing Clients, potential employees, and subcontractors.

Industry/Entity Type

Business

Colors

Designer to choose colors to be used in the design.

Requirements
Nice to have
• I just want something that's more pleasing to the eye. You can use a combination of either / or of my logos.

```html
<!DOCTYPE html>
<html lang="en">
<head>
<meta charset="utf-8">
<title>Sturdy Crew Builders – Business Card</title>
<link rel="stylesheet" href="https://fonts.googleapis.com/css2?family=Abel&family=Bebas+Neue&display=swap">
<style>
  :root {
    --backdrop: #3a3a3a;
    --card-white: #f1f1f1;
    --brown: #3f140d;
    --orange: #e8711f;
    --orange-light: #f2ad3a;
    --yellow: #eab51b;
    --grey-text: #555555;
    --divider: #c9c9c9;
    --white: #ffffff;
  }
  * { margin: 0; padding: 0; box-sizing: border-box; }
  html, body { width: 1200px; height: 960px; overflow: hidden; }
  body { background: var(--backdrop); position: relative; font-family: "Abel", sans-serif; }

  .card { position: absolute; width: 600px; height: 343px; overflow: hidden; }
  .card-front { left: 320px; top: 103px; background: linear-gradient(135deg, #e4e4e4 0%, var(--card-white) 40%, #f7f7f7 100%); }
  .card-back { left: 317px; top: 488px; background: linear-gradient(130deg, var(--orange-light) 0%, var(--orange) 45%, var(--orange) 100%); }

  .brand { position: absolute; left: 50px; top: 112px; display: flex; align-items: center; gap: 10px; }
  .brand-mark { width: 44px; height: 44px; border-radius: 50%; background: var(--brown); flex: none; }
  .brand-name { font-family: "Abel", sans-serif; color: var(--brown); font-size: 30px; line-height: 30px; font-weight: 400; }

  .divider { position: absolute; left: 311px; top: 72px; width: 1px; height: 170px; background: var(--divider); }

  .contact { position: absolute; left: 339px; top: 66px; }
  .person-name { font-family: "Bebas Neue", sans-serif; font-size: 32px; line-height: 32px; color: var(--brown); letter-spacing: 0.5px; }
  .person-role { font-size: 16px; line-height: 19px; color: var(--orange); }
  .address { margin-top: 9px; font-size: 15px; line-height: 18px; color: var(--grey-text); }
  .contact-list { margin-top: 9px; list-style: none; }
  .contact-list li { display: flex; align-items: center; gap: 8px; font-size: 15px; line-height: 19px; color: var(--grey-text); }
  .contact-list svg { width: 13px; height: 13px; fill: var(--brown); flex: none; }

  .stripes { position: absolute; left: 0; bottom: 0; width: 600px; height: 34px; }
  .front-web { position: absolute; right: 18px; bottom: 9px; color: var(--white); font-size: 16px; letter-spacing: 3px; }

  .emblem { position: absolute; left: 208px; top: 69px; width: 190px; height: 190px; border-radius: 50%; background: var(--brown); border: 3px solid var(--white); }
  .back-web { position: absolute; left: 0; width: 100%; top: 292px; text-align: center; color: var(--white); font-size: 16px; letter-spacing: 3px; }
</style>
</head>
<body>
  <section class="card card-front">
    <div class="brand">
      <span class="brand-mark"></span>
      <span class="brand-name">Sturdy Crew<br>Builders, Inc.</span>
    </div>
    <div class="divider"></div>
    <div class="contact">
      <h1 class="person-name">Sam Carver</h1>
      <p class="person-role">Apex Certified Roof Inspector</p>
      <p class="person-role">Licensed Property Adjuster</p>
      <p class="address">4810 Maple Ridge Drive Suite 110<br>Plano, TX 75093</p>
      <ul class="contact-list">
        <li><svg viewBox="0 0 24 24"><path d="M6.6 10.8a15.1 15.1 0 0 0 6.6 6.6l2.2-2.2c.3-.3.7-.4 1-.2 1.1.4 2.3.6 3.6.6.6 0 1 .4 1 1V20c0 .6-.4 1-1 1A17 17 0 0 1 3 4c0-.6.4-1 1-1h3.5c.6 0 1 .4 1 1 0 1.3.2 2.5.6 3.6.1.3 0 .7-.2 1z"/></svg>(555) 010-2400</li>
        <li><svg viewBox="0 0 24 24"><path d="M7 1h10a2 2 0 0 1 2 2v18a2 2 0 0 1-2 2H7a2 2 0 0 1-2-2V3a2 2 0 0 1 2-2zm0 3v14h10V4zm5 15.5a1 1 0 1 0 0 2 1 1 0 0 0 0-2z"/></svg>(555) 010-7788</li>
        <li><svg viewBox="0 0 24 24"><path d="M2 5h20v14H2zm2 2v.5l8 5 8-5V7l-8 5z"/></svg>sam@sturdycrewtx.com</li>
      </ul>
    </div>
    <svg class="stripes" viewBox="0 0 600 34" aria-hidden="true">
      <polygon points="0,12 188,12 182,21 0,21" fill="var(--yellow)"/>
      <polygon points="192,12 358,12 352,21 186,21" fill="var(--orange)"/>
      <polygon points="370,0 600,0 600,34 340,34" fill="var(--brown)"/>
    </svg>
    <span class="front-web">www.sturdycrewtx.com</span>
  </section>

  <section class="card card-back">
    <span class="emblem"></span>
    <p class="back-web">www.sturdycrewtx.com</p>
  </section>
</body>
</html>
```